Local massage therapist needs some new marketing material

Hi there! I am a massage therapist here in Denver, CO in Alder Bend(shopping and art district) of the city. My business is called Lumo Bodywork of Denver. My practice has an eastern influence and I do reflexology, thai massage and use Chinese herbs, etc. I know all my clients and pay close attention to details. I am also very respectful of tradition and it shows in how I work. I tend to like modern, clean, fun, Asian designs. I am wanting a new business card and brochure. I have a logo and branding for my business that I want used in the design. Currently, the sign for my building is purple and I think my logo was designed to be purple. I will attach pictures of it and can send whatever files are necessary so it can be integrated into the brochure, etc. I like the purple but open to using other colors as well. Thanks!
My website is lumobodyworkofdenver.example where info can be gathered about me and services/fees for brochure.
Updates

Just increased budget. Please see new feedback in discussion thread.

Thanks!

                                       HEY ALL,

Just wanted to let you know that I made a change to my website. It is on the Prices Page. I no longer have the frequent  flyer prices but I added discounts. Let me know if you have any questions. Thanks so much!

Target Market(s)

healthy, urban, educated, upper middle class, yogis

Industry/Entity Type

Marketing

Requirements
Must have
• logo stays purple
Should not have
• not too busy

```html
<!DOCTYPE html>
<html lang="en">
<head>
<meta charset="utf-8">
<title>Lumo Bodywork of Denver – Business Card</title>
<link href="https://fonts.googleapis.com/css2?family=Open+Sans:ital,wght@0,400;0,600;0,700;1,400&display=swap" rel="stylesheet">
<style>
  :root {
    --purple: #662d91;
    --purple-deep: #5a2585;
    --ink: #4a4a4a;
    --muted: #6e6e6e;
    --rule: #9a9a9a;
    --card: #ffffff;
    --backdrop: #e9e8ef;
    --swoosh: #2b2b2b;
  }
  * { box-sizing: border-box; margin: 0; padding: 0; }
  html, body {
    width: 1200px; height: 987px; overflow: hidden;
    background: var(--backdrop);
    font-family: "Open Sans", Arial, sans-serif;
  }
  .stage { position: relative; width: 1200px; height: 987px; }
  .card {
    position: absolute; top: 339px;
    width: 540px; height: 309px;
    background: var(--card);
    border-radius: 26px;
    overflow: hidden;
    box-shadow: 0 10px 28px rgba(60, 50, 90, 0.18);
  }
  .card--front { left: 40px; }
  .card--back { left: 620px; }

  /* Front */
  .brand {
    position: absolute; left: 0; right: 0; top: 46px;
    display: flex; align-items: center; justify-content: center; gap: 14px;
  }
  .brand__dot {
    width: 34px; height: 34px; border-radius: 50%;
    background: var(--purple);
  }
  .brand__name {
    font-weight: 600; font-size: 64px; letter-spacing: 10px;
    color: var(--purple); line-height: 1;
  }
  .person {
    position: absolute; top: 132px; left: 0; right: 0; text-align: center;
    font-size: 20px; color: var(--ink);
  }
  .person__name { font-weight: 700; color: var(--purple); }
  .band { position: absolute; left: 0; bottom: 0; width: 540px; height: 140px; }
  .contact {
    position: absolute; left: 18px; right: 18px; bottom: 24px;
    color: #fff; font-size: 12.5px; line-height: 1.75; text-align: center;
    white-space: nowrap;
  }
  .contact__row { display: flex; justify-content: center; align-items: center; gap: 6px; }
  .contact__item { display: inline-flex; align-items: center; gap: 6px; }
  .contact__item + .contact__item { margin-left: 8px; }
  .contact__icon { width: 13px; height: 13px; flex: none; }

  /* Back */
  .appt {
    position: absolute; left: 34px; top: 28px; right: 34px;
    color: var(--ink); font-size: 15px;
  }
  .appt__title {
    font-weight: 700; font-size: 14px; letter-spacing: 0.5px;
    color: var(--purple); text-transform: uppercase; margin-bottom: 14px;
  }
  .field { display: flex; align-items: flex-end; gap: 6px; height: 28px; }
  .field__line { flex: 1; border-bottom: 1px dotted var(--rule); height: 1px; margin-bottom: 5px; }
  .field__line--short { flex: 0 0 170px; }
  .field__unit { white-space: nowrap; }
  .hours { margin-top: 14px; font-size: 14.5px; line-height: 1.5; width: 300px; }
  .note { margin-top: 6px; font-size: 13px; font-style: italic; color: var(--muted); width: 300px; }
  .brand--small {
    top: auto; bottom: 36px; left: auto; right: 30px; gap: 10px;
  }
  .brand--small .brand__dot { width: 22px; height: 22px; }
  .brand--small .brand__name { font-size: 42px; letter-spacing: 6px; }
</style>
</head>
<body>
<main class="stage">

  <section class="card card--front" aria-label="Business card front">
    <div class="brand">
      <span class="brand__dot" aria-hidden="true"></span>
      <span class="brand__name">LUMO</span>
    </div>
    <p class="person"><span class="person__name">Your Name,</span> Title</p>

    <svg class="band" viewBox="0 0 540 140" preserveAspectRatio="none" aria-hidden="true">
      <path d="M0 6 Q270 40 540 6 L540 12 Q270 48 0 12 Z" fill="var(--swoosh)"/>
      <path d="M0 14 Q270 52 540 14 L540 140 L0 140 Z" fill="var(--purple)"/>
    </svg>

    <div class="contact">
      <div class="contact__row">1450 E 4th Ave, Denver, CO 80218</div>
      <div class="contact__row">
        <svg class="contact__icon" viewBox="0 0 16 16" aria-hidden="true"><circle cx="8" cy="8" r="8" fill="#fff"/><path d="M5 4h2l1 2.5-1.2 1a6 6 0 0 0 2.7 2.7l1-1.2L13 10v2a1 1 0 0 1-1 1A9 9 0 0 1 4 5a1 1 0 0 1 1-1z" fill="var(--purple)" transform="scale(.8) translate(2 2)"/></svg>
        303.555.0142
      </div>
      <div class="contact__row">
        <span class="contact__item">
          <svg class="contact__icon" viewBox="0 0 16 16" aria-hidden="true"><rect x="1" y="3" width="14" height="10" rx="1.5" fill="#fff"/><path d="M2 4l6 5 6-5" stroke="var(--purple)" stroke-width="1.4" fill="none"/></svg>
          info@lumobodyworkofdenver.example
        </span>
        <span class="contact__item">
          <svg class="contact__icon" viewBox="0 0 16 16" aria-hidden="true"><circle cx="8" cy="8" r="7" fill="#fff"/><path d="M1 8h14M8 1c-3 3.5-3 10.5 0 14M8 1c3 3.5 3 10.5 0 14" stroke="var(--purple)" stroke-width="1.1" fill="none"/></svg>
          www.lumobodyworkofdenver.example
        </span>
      </div>
    </div>
  </section>

  <section class="card card--back" aria-label="Business card back">
    <div class="appt">
      <h2 class="appt__title">Your Appointment</h2>
      <div class="field"><span>Name :</span><span class="field__line"></span></div>
      <div class="field"><span>Date :</span><span class="field__line field__line--short"></span><span>Time :</span><span class="field__line"></span><span class="field__unit">am / pm</span></div>
      <p class="hours">Tues - Fri 10am - 8pm Sat 10am-5pm (Appointments required) No walk-ins please.</p>
      <p class="note">We appreciate a 24 hr. notice for cancellations</p>
    </div>
    <div class="brand brand--small">
      <span class="brand__dot" aria-hidden="true"></span>
      <span class="brand__name">LUMO</span>
    </div>
  </section>

</main>
</body>
</html>
```